Simple Logo Design for Semi-Clear Plastic Frosted Card stock

Create a business card on frosted plastic. compliment existing logo elements with a tree trunk, roots, or seed at the lower half and the full logo both on the front.

Contact information will go on a solid portion of the back of this design since this card stock is semi-transparent.

It is important to consider this plastic card stock medium in your design. I found helpful tips and guides listed at vellaprint-sample.net: be careful to understand ink printed on plastic cards cannot have too much of a consistent print area or risks peeling and fine lines can easily scratch off.
Updates

2" x 3.5" 20PT Clear Plastic Business cards with Round corners Please get info or templates here: https://www.vellaprint-sample.net/product-detail/2-x-35-20pt-clear-plastic-business-cards-with-round-corners

Target Market(s)

Not for profit- religion

Industry/Entity Type

Business

Must include complementary elements to the existing logo

Font styles to use
Decorative

Colors
000000

Requirements
Must have
• Elements of community, nature and oneness. Such as: seed, roots, tree trunk, etc.
• Three lines of space on the back for Name, Title, Phone Number.
Nice to have
• I like a light use of decorative elements
Should not have
• No eyes, from faces or animals.

```html
<!DOCTYPE html>
<html lang="en">
<head>
<meta charset="utf-8">
<title>Hopeful Roots – Business Card</title>
<link rel="stylesheet" href="https://fonts.googleapis.com/css2?family=Josefin+Sans:wght@400;600&family=Arimo:wght@400&display=swap">
<style>
  :root {
    --page-bg: #e6e2dc;
    --card-frost-top: #f3f2ef;
    --card-frost-bottom: #e2e0db;
    --brand-teal: #2f5f5c;
    --tagline-grey: #55585a;
    --band-green: #3f8a2e;
    --band-teal: #1f5449;
    --band-teal-deep: #173f39;
    --name-gold: #d8cdb2;
    --title-gold: #cfc4aa;
  }
  * { margin: 0; padding: 0; box-sizing: border-box; }
  html, body {
    width: 1200px;
    height: 970px;
    overflow: hidden;
    background: var(--page-bg);
  }
  .canvas {
    position: relative;
    width: 1200px;
    height: 970px;
  }
  .card {
    position: absolute;
    left: 75px;
    top: 172px;
    width: 1050px;
    height: 626px;
    border-radius: 28px;
    overflow: hidden;
    background: linear-gradient(160deg, var(--card-frost-top) 0%, var(--card-frost-bottom) 100%);
    box-shadow: 0 18px 40px rgba(60, 50, 40, 0.18), inset 0 0 0 1px rgba(255,255,255,0.6);
  }
  .card-wave {
    position: absolute;
    inset: 0;
    width: 100%;
    height: 100%;
  }
  .brand {
    position: absolute;
    left: 50px;
    top: 70px;
    width: 530px;
    text-align: center;
  }
  .brand-dot {
    width: 160px;
    height: 160px;
    margin: 0 auto 28px;
    border-radius: 50%;
    background: var(--brand-teal);
  }
  .brand-name {
    font-family: "Josefin Sans", sans-serif;
    font-weight: 400;
    font-size: 60px;
    letter-spacing: 1px;
    line-height: 1;
    color: var(--brand-teal);
    white-space: nowrap;
  }
  .brand-tagline {
    margin-top: 8px;
    font-family: "Josefin Sans", sans-serif;
    font-weight: 600;
    font-size: 21px;
    letter-spacing: 1.5px;
    color: var(--tagline-grey);
    white-space: nowrap;
  }
  .contact {
    position: absolute;
    right: 55px;
    top: 418px;
    text-align: right;
    font-family: "Arimo", sans-serif;
    white-space: nowrap;
  }
  .contact-name {
    font-size: 52px;
    color: var(--name-gold);
    line-height: 1;
  }
  .contact-title {
    margin-top: 14px;
    font-size: 30px;
    color: var(--title-gold);
    line-height: 1;
  }
  .contact-phone {
    margin-top: 44px;
    font-size: 30px;
    color: var(--title-gold);
    line-height: 1;
    display: flex;
    align-items: center;
    justify-content: flex-end;
    gap: 18px;
  }
  .phone-icon { width: 22px; height: 22px; }
</style>
</head>
<body>
<main class="canvas">
  <section class="card" aria-label="Frosted plastic business card">
    <svg class="card-wave" viewBox="0 0 1050 626" preserveAspectRatio="none" aria-hidden="true">
      <defs>
        <linearGradient id="bandFill" x1="0" y1="0" x2="1" y2="1">
          <stop offset="0" stop-color="var(--band-teal)"/>
          <stop offset="1" stop-color="var(--band-teal-deep)"/>
        </linearGradient>
      </defs>
      <path d="M110 626 C 420 490, 720 310, 1050 295 L 1050 626 Z" fill="var(--band-green)"/>
      <path d="M150 626 C 450 510, 750 340, 1050 328 L 1050 626 Z" fill="url(#bandFill)" opacity="0.95"/>
    </svg>

    <div class="brand">
      <div class="brand-dot"></div>
      <div class="brand-name">HOPEFUL ROOTS</div>
      <div class="brand-tagline">FAITH, FELLOWSHIP &amp; GROWTH</div>
    </div>

    <div class="contact">
      <div class="contact-name">Daniel Hartwell</div>
      <div class="contact-title">Managing Director</div>
      <div class="contact-phone">
        <span>0400 123 456</span>
        <svg class="phone-icon" viewBox="0 0 24 24" aria-hidden="true">
          <path d="M3 9 C3 5 21 5 21 9 L21 11 L16 11 L16 9 L8 9 L8 11 L3 11 Z" fill="var(--title-gold)"/>
          <rect x="5" y="13" width="14" height="8" rx="1.5" fill="var(--title-gold)"/>
        </svg>
      </div>
    </div>
  </section>
</main>
</body>
</html>
```